Ductless Mini Split Business Website

Copper Fern Services is looking to design an eye catching educational website about installing Ductless mini splits.

Similar to this company.
https://www.halvikstream.com/

Coding

Coded - Design and coding required

```html
<!DOCTYPE html>
<html lang="en">
<head>
<meta charset="utf-8">
<title>Copper Fern Services – Ductless Experts</title>
<link href="https://fonts.googleapis.com/css2?family=Bungee&family=Montserrat:wght@700;800&family=Roboto:wght@400;500;700&display=swap" rel="stylesheet">
<style>
:root{
  --yellow:#fdcb0a;
  --yellow-deep:#f2bd00;
  --ink:#1d1d1d;
  --dark:#3b3b3d;
  --footer:#202020;
  --text:#555;
  --muted:#8a8a8a;
  --light:#f2f2f2;
  --white:#fff;
}
*{box-sizing:border-box;margin:0;padding:0}
html,body{width:1200px;height:5324px;overflow:hidden}
body{position:relative;background:var(--white);font-family:"Roboto",sans-serif;color:var(--text)}
.abs{position:absolute}
.display{font-family:"Bungee",sans-serif;text-transform:uppercase;color:var(--ink);letter-spacing:.5px}
.btn{position:absolute;display:flex;align-items:center;justify-content:center;gap:8px;background:var(--yellow);color:var(--ink);font:700 14px "Roboto",sans-serif;text-transform:uppercase;border-radius:30px}
.btn .dot{width:14px;height:14px;border-radius:50%;background:var(--ink);position:relative}
.btn .dot::after{content:"";position:absolute;left:4px;top:4px;border-left:6px solid var(--yellow);border-top:3px solid transparent;border-bottom:3px solid transparent}
.ph{position:absolute}

/* header */
.brand{position:absolute;left:112px;top:22px;display:flex;align-items:center;gap:10px}
.brand-mark{width:34px;height:34px;border-radius:50%;background:var(--yellow)}
.brand-name{font:700 22px "Roboto",sans-serif;color:var(--ink);line-height:1}
.brand-tag{position:absolute;left:118px;top:78px;font:700 17px "Roboto",sans-serif;color:var(--ink);letter-spacing:.5px}
.search{position:absolute;left:602px;top:42px;width:256px;height:34px;border:1px solid #cfcfcf;border-radius:18px;background:#f6f6f6;font-size:12px;color:var(--muted);padding:9px 16px}
.search svg{position:absolute;right:14px;top:10px}
.call{position:absolute;left:930px;top:38px;width:250px;text-align:center;color:var(--ink)}
.call .lbl{font-size:13px}
.call .num{font:700 23px "Roboto",sans-serif;margin-top:6px}
.call .now{font-size:10px;text-decoration:underline;margin-top:8px;margin-left:90px}
.nav{position:absolute;left:0;top:118px;height:35px;display:flex;gap:22px;padding-left:110px;align-items:center}
.nav a{font:500 13.5px "Roboto",sans-serif;color:var(--white);text-decoration:none;position:relative}
.nav a.active{color:var(--yellow)}
.nav a.active::after{content:"";position:absolute;left:0;right:0;bottom:-8px;height:2px;background:var(--yellow)}

/* hero */
.hero-title{position:absolute;left:0;width:1200px;top:312px;text-align:center;font-size:56px;color:var(--ink)}
.hero-sub{position:absolute;left:290px;width:620px;top:400px;text-align:center;font-size:18px;line-height:29px;color:var(--ink)}
.arrow-circle{position:absolute;width:40px;height:40px;border:2px solid rgba(255,255,255,.85);border-radius:50%}

/* about */
.about-title{position:absolute;left:618px;top:984px;font-size:38px}
.about-copy{position:absolute;left:618px;top:1052px;width:470px;font-size:13.5px;line-height:27.5px;color:#777;text-align:justify}

/* comfort */
.comfort-title{position:absolute;left:0;width:1200px;top:1565px;text-align:center;font-size:33px;color:var(--yellow)}
.feature{position:absolute;top:1655px;width:300px;text-align:center}
.feature .ico{width:124px;height:124px;margin:0 auto;border-radius:50%;background:var(--yellow);border:4px solid var(--dark);box-shadow:0 0 0 3px var(--yellow);display:flex;align-items:center;justify-content:center}
.feature h3{margin-top:26px;font:500 20px "Roboto",sans-serif;color:var(--white);text-transform:uppercase}
.feature p{margin-top:14px;font-size:14px;line-height:24px;color:#d8d8d8}

/* help */
.sec-title{position:absolute;left:0;width:1200px;text-align:center;font-size:34px}
.svc{position:absolute;width:312px;height:194px;background:var(--white);box-shadow:0 2px 8px rgba(0,0,0,.18);padding:5px}
.svc .pic{width:100%;height:100%;position:relative}
.svc .cap{position:absolute;left:0;right:0;bottom:14px;text-align:center;font:500 17px "Roboto",sans-serif;color:var(--white);line-height:28px}

/* why */
.why-title{position:absolute;left:672px;top:2840px;font-size:34px;color:var(--yellow)}
.why-item{position:absolute;left:672px;width:400px}
.why-item h4{display:flex;align-items:center;gap:14px;font:500 15px "Roboto",sans-serif;color:var(--white)}
.why-item p{margin-top:18px;font-size:13.5px;line-height:24px;color:#e6e6e6}

/* contact */
.kicker{position:absolute;left:0;width:1200px;top:3412px;text-align:center;font:500 16px "Roboto",sans-serif;color:var(--ink);text-transform:uppercase}
.contact-title{position:absolute;left:0;width:1200px;top:3440px;text-align:center;font:800 37px "Montserrat",sans-serif;color:var(--ink);text-transform:uppercase}
.contact-call{position:absolute;left:0;width:1200px;top:3494px;text-align:center;font-size:16px;color:var(--ink)}
.contact-call b{font-size:24px}
.field{position:absolute;height:42px;background:#e9e9e9;border:1px solid #d3d3d3;font-size:14px;color:#888;padding:12px 16px}
.robot{position:absolute;left:218px;top:3790px;display:flex;align-items:center;gap:12px;font-size:14px;color:#666}
.robot .box{width:20px;height:20px;border:2px solid #666;border-radius:2px}
.captcha{position:absolute;left:395px;top:3776px;width:54px;text-align:center;font-size:9px;color:#999}
.captcha span{display:block;width:34px;height:34px;margin:0 auto 4px;border-radius:4px;background:#c9d2e3}

/* testimonials */
.t-card{position:absolute;left:210px;top:4085px;width:780px;height:254px;background:var(--white);box-shadow:0 2px 10px rgba(0,0,0,.12)}
.t-card h2{position:absolute;left:0;width:780px;top:26px;text-align:center;font:700 32px "Montserrat",sans-serif;color:var(--ink)}
.t-quote{position:absolute;left:196px;top:102px;width:560px;font-size:14px;line-height:23px;font-style:italic;color:#666}
.t-name{position:absolute;left:196px;top:186px;font:500 16px "Roboto",sans-serif;color:var(--ink)}
.t-co{position:absolute;left:196px;top:212px;font-size:11px;color:#888}
.qmark{position:absolute;font:700 54px Georgia,serif;color:#bbb;line-height:1}
.chev{position:absolute;font:400 34px "Roboto",sans-serif;color:var(--ink)}

/* stand behind */
.res{position:absolute;top:4520px;width:312px;height:368px;background:var(--white);box-shadow:0 2px 8px rgba(0,0,0,.15);border-bottom:5px solid var(--yellow);padding:5px}
.res .pic{width:100%;height:178px}
.res h4{margin-top:36px;text-align:center;font:500 18px "Roboto",sans-serif;color:var(--ink);text-transform:uppercase}
.res .btn{position:relative;margin:20px auto 0;width:168px;height:38px;font-size:13px}

/* footer */
.footer{position:absolute;left:0;top:4960px;width:1200px;height:364px;background:var(--footer)}
.f-head{position:absolute;top:50px;font:500 18px "Roboto",sans-serif;color:var(--white);text-transform:uppercase}
.f-line{position:absolute;display:flex;gap:16px;font-size:13px;line-height:20px;color:#ddd}
.f-div{position:absolute;top:40px;width:1px;height:150px;background:#555}
.f-brand{position:absolute;left:140px;top:80px;display:flex;align-items:center;gap:10px}
.f-brand .brand-name{color:var(--yellow);font-size:22px}
.f-tag{position:absolute;left:145px;top:150px;font:700 17px "Roboto",sans-serif;color:var(--yellow);letter-spacing:.5px}
.social{position:absolute;left:140px;top:198px;display:flex;gap:22px}
.social span{width:22px;height:22px;border-radius:50%;background:var(--white)}
.news-txt{position:absolute;left:816px;top:92px;width:290px;font-size:11px;line-height:19px;color:#ddd}
.news-input{position:absolute;left:816px;top:146px;width:274px;height:32px;background:var(--white);border-radius:16px;font-size:11px;color:#888;padding:9px 16px}
.copyright{position:absolute;left:0;width:1200px;top:320px;text-align:center;font-size:12px;color:#ddd}
.f-rule{position:absolute;left:112px;top:280px;width:976px;height:1px;background:#555}
</style>
</head>
<body>

<!-- header -->
<header>
  <div class="brand"><span class="brand-mark"></span><span class="brand-name">Copper Fern Services</span></div>
  <div class="brand-tag">DUCTLESS EXPERTS</div>
  <div class="search">Search
    <svg width="14" height="14" viewBox="0 0 14 14"><circle cx="6" cy="6" r="4.5" fill="none" stroke="#444" stroke-width="1.8"/><line x1="9.3" y1="9.3" x2="13" y2="13" stroke="#444" stroke-width="1.8"/></svg>
  </div>
  <svg class="abs" style="left:0;top:118px" width="1200" height="35"><rect width="900" height="35" fill="#000"/></svg>
  <svg class="abs" style="left:0;top:0" width="1200" height="153"><polygon points="912,0 1200,0 1200,153 886,153" fill="var(--yellow)"/></svg>
  <div class="call">
    <div class="lbl"><svg width="16" height="16" viewBox="0 0 24 24" style="vertical-align:-3px;margin-right:6px"><circle cx="12" cy="12" r="12" fill="#1d1d1d"/><path d="M8 6l2.5 0 1 3-1.5 1.2a8 8 0 0 0 3.8 3.8L15 12.5l3 1v2.5a1.5 1.5 0 0 1-1.5 1.5A10.5 10.5 0 0 1 6.5 7.5 1.5 1.5 0 0 1 8 6z" fill="var(--yellow)"/></svg>Call Us Today</div>
    <div class="num">(555)010 2468</div>
    <div class="now">Onsite Immediately!</div>
  </div>
  <nav class="nav">
    <a class="active">Home</a><a>About Us</a><a>Ductless Heat Pumps</a><a>FAQ</a><a>Financing</a><a>Reviews</a><a>Contact Us</a>
    <a style="margin-left:6px"><svg width="9" height="12" viewBox="0 0 10 14" style="vertical-align:-1px;margin-right:5px"><path d="M5 0a5 5 0 0 1 5 5c0 4-5 9-5 9S0 9 0 5a5 5 0 0 1 5-5z" fill="#fff"/><circle cx="5" cy="5" r="2" fill="#000"/></svg>Locations</a>
  </nav>
</header>

<!-- hero -->
<section>
  <svg class="abs" style="left:0;top:153px" width="1200" height="680" role="img" aria-label="Photo of a man relaxing on a sofa beneath a wall-mounted ductless unit">
    <defs><linearGradient id="heroBg" x1="0" y1="0" x2="1" y2="0"><stop offset="0" stop-color="#b8a795"/><stop offset=".5" stop-color="#e6e2dc"/><stop offset="1" stop-color="#cfc9c2"/></linearGradient></defs>
    <polygon points="0,0 1200,0 1200,470 1010,662 0,467" fill="url(#heroBg)"/>
    <polygon points="1200,455 1200,520 1045,662 1010,662" fill="var(--yellow)"/>
  </svg>
  <div class="arrow-circle" style="left:34px;top:358px"><svg width="36" height="36"><polyline points="21,11 14,18 21,25" fill="none" stroke="#fff" stroke-width="2"/></svg></div>
  <div class="arrow-circle" style="left:1128px;top:358px"><svg width="36" height="36"><polyline points="15,11 22,18 15,25" fill="none" stroke="#fff" stroke-width="2"/></svg></div>
  <h1 class="display hero-title">Copper Fern Services</h1>
  <p class="hero-sub">Lorem ipsum dolor sit amet, consectetur adipiscing elit, sed do eiusmod tempor incididunt ut labore et dolore magna aliqua.</p>
  <div class="btn" style="left:501px;top:490px;width:198px;height:52px;font-size:16px">Get Started <span class="dot"></span></div>
  <div class="ph" role="img" aria-label="Mascot illustration holding a remote" style="left:940px;top:800px;width:205px;height:175px;border-radius:50%;background:radial-gradient(circle,#f7d64a 0,#e8c23a 50%,rgba(255,255,255,0) 72%)"></div>
</section>

<!-- about -->
<section>
  <svg class="abs" style="left:118px;top:895px" width="432" height="496" role="img" aria-label="Photo of a technician servicing an indoor unit while a homeowner watches">
    <polygon points="216,4 428,126 428,370 216,492 4,370 4,126" fill="#c9cfd6" stroke="var(--yellow)" stroke-width="5"/>
  </svg>
  <h2 class="display about-title">About Us</h2>
  <p class="about-copy">Sed ut perspiciatis unde omnis iste natus error sit voluptatem accusantium doloremque laudantium, totam rem aperiam, eaque ipsa quae ab illo inventore veritatis et quasi architecto beatae vitae sunt explicabo. Nemo enim ipsam voluptatem quia voluptas sit aspernatur aut odit aut fugit, sed quia consequuntur magni dolores eos qui ratione voluptatem sequi nesciunt. Neque porro quisquam est, qui dolorem ipsum quia</p>
  <div class="btn" style="left:618px;top:1280px;width:168px;height:50px;font-size:13px">Learn More <span class="dot"></span></div>
</section>

<!-- comfort -->
<section>
  <svg class="abs" style="left:0;top:1507px" width="1200" height="484">
    <rect width="1200" height="484" fill="var(--dark)"/>
    <polygon points="0,472 1200,422 1200,484 0,484" fill="var(--yellow)"/>
  </svg>
  <h2 class="display comfort-title">Copper Fern Services Comfort Made Easy</h2>
  <div class="feature" style="left:99px">
    <div class="ico"><svg width="64" height="64" viewBox="0 0 64 64" fill="none" stroke="#1d1d1d" stroke-width="3"><rect x="10" y="14" width="44" height="16" rx="3"/><path d="M22 30v14a4 4 0 0 0 8 0V30M36 30v20M42 30v12"/><circle cx="18" cy="22" r="3"/></svg></div>
    <h3>Easy to Install</h3>
    <p>Lorem ipsum dolor sit amet, consectetur adipiscing elit, sed do eiusmod tempor</p>
  </div>
  <div class="feature" style="left:448px">
    <div class="ico"><svg width="64" height="64" viewBox="0 0 64 64" fill="none" stroke="#1d1d1d" stroke-width="3"><rect x="8" y="12" width="48" height="18" rx="3"/><line x1="12" y1="24" x2="52" y2="24"/><path d="M24 38v12M18 44h12M40 38v12M34 44h12"/></svg></div>
    <h3>Easy to Own</h3>
    <p>Lorem ipsum dolor sit amet, consectetur adipiscing elit, sed do eiusmod tempor</p>
  </div>
  <div class="feature" style="left:796px">
    <div class="ico"><svg width="64" height="64" viewBox="0 0 64 64" fill="none" stroke="#1d1d1d" stroke-width="3"><rect x="8" y="30" width="48" height="16" rx="3"/><line x1="12" y1="40" x2="52" y2="40"/><path d="M40 10v20M34 18h12"/></svg></div>
    <h3>Easy to Service</h3>
    <p>Lorem ipsum dolor sit amet, consectetur adipiscing elit, sed do eiusmod tempor</p>
  </div>
</section>

<!-- how can we help -->
<section>
  <h2 class="display sec-title" style="top:2086px">How Can We Help You?</h2>
  <div class="svc" style="left:110px;top:2162px"><div class="pic" role="img" aria-label="Photo of an outdoor condenser unit" style="background:linear-gradient(160deg,#6d7a6b,#9ca4a0)"><div class="cap">Baseboard Heat Replacement</div></div></div>
  <div class="svc" style="left:444px;top:2162px"><div class="pic" role="img" aria-label="Photo of a technician at an exterior heat pump" style="background:linear-gradient(160deg,#a7a09a,#5d6b82)"><div class="cap">Ductless Heat Pump FAQ</div></div></div>
  <div class="svc" style="left:778px;top:2162px"><div class="pic" role="img" aria-label="Photo of a woman relaxing with a remote in a living room" style="background:linear-gradient(160deg,#d9dbd8,#8d9491)"><div class="cap" style="bottom:8px">Ductless for Additions &amp;<br>Remodels</div></div></div>
  <div class="svc" style="left:110px;top:2384px"><div class="pic" role="img" aria-label="Photo of hands installing an indoor unit" style="background:linear-gradient(160deg,#e3e5e8,#4d6a94)"><div class="cap">Ductless Installation</div></div></div>
  <div class="svc" style="left:444px;top:2384px"><div class="pic" role="img" aria-label="Photo of a technician maintaining a unit" style="background:linear-gradient(160deg,#b8bcc2,#3f5f8c)"><div class="cap">Ductless Maintenance</div></div></div>
  <div class="svc" style="left:778px;top:2384px"><div class="pic" role="img" aria-label="Photo of a woman resting under a cooling unit" style="background:linear-gradient(160deg,#dcdcd8,#9a9690)"><div class="cap">Ductless Warranty</div></div></div>
  <div class="btn" style="left:475px;top:2637px;width:250px;height:46px;font-size:13px">More Ductless Services <span class="dot"></span></div>
</section>

<!-- why choose -->
<section>
  <svg class="abs" style="left:0;top:2793px" width="1200" height="510">
    <rect width="620" height="510" fill="#c8b6a8" role="img" aria-label="Photo of a couple on a sofa beneath a ductless unit"/>
    <polygon points="510,0 1200,0 1200,510 560,510" fill="var(--dark)"/>
    <polygon points="500,0 516,0 566,510 548,510" fill="var(--yellow)"/>
  </svg>
  <h2 class="display why-title">Why Choose</h2>
  <div class="why-item" style="top:2922px">
    <h4><svg width="24" height="26" viewBox="0 0 24 26" fill="none" stroke="var(--yellow)" stroke-width="2"><rect x="4" y="2" width="16" height="22" rx="2"/><path d="M8 8h8M8 12h8M8 16h5"/></svg>0% Financing for 60 months</h4>
    <p>Lorem ipsum dolor sit amet, consectetur adipiscing elit, sed do eiusmod tempor incididunt</p>
  </div>
  <div class="why-item" style="top:3042px">
    <h4><svg width="26" height="24" viewBox="0 0 26 24" fill="none" stroke="var(--yellow)" stroke-width="2"><circle cx="13" cy="12" r="9"/><path d="M9 12l3 3 5-6"/></svg>365 Day, Money Back Guarantee</h4>
    <p>Lorem ipsum dolor sit amet, consectetur adipiscing elit, sed do eiusmod tempor incididunt</p>
  </div>
  <div class="why-item" style="top:3158px">
    <h4><svg width="26" height="24" viewBox="0 0 26 24" fill="none" stroke="var(--yellow)" stroke-width="2"><rect x="3" y="4" width="16" height="16" rx="2"/><path d="M7 12l4 4 12-13"/></svg>We Are the Experts in Ductless Services</h4>
    <p>Lorem ipsum dolor sit amet, consectetur adipiscing elit, sed do eiusmod tempor incididunt</p>
  </div>
</section>

<!-- contact -->
<section>
  <div class="abs" style="left:0;top:3302px;width:1200px;height:633px;background:var(--light)"></div>
  <div class="kicker">Copper Fern Services</div>
  <h2 class="contact-title">We Invite You to Contact Us</h2>
  <p class="contact-call">Call Us Today: <b>(555) 010 2468</b></p>
  <div class="field" style="left:188px;top:3550px;width:400px">Name</div>
  <div class="field" style="left:608px;top:3550px;width:404px">Email</div>
  <div class="field" style="left:188px;top:3607px;width:400px">Phone</div>
  <div class="field" style="left:608px;top:3607px;width:404px">subjects</div>
  <div class="field" style="left:188px;top:3664px;width:824px;height:84px">Message</div>
  <div class="robot"><span class="box"></span>I'm not a Robot</div>
  <div class="captcha"><span></span>reCAPTCHA</div>
  <div class="btn" style="left:553px;top:3790px;width:106px;height:36px;font-size:13px">Submit</div>
</section>

<!-- testimonials -->
<section>
  <svg class="abs" style="left:0;top:3935px" width="1200" height="550">
    <rect y="0" width="1200" height="550" fill="var(--light)"/>
    <polygon points="0,0 1200,0 1200,26 0,40" fill="var(--yellow)"/>
    <rect y="30" width="1200" height="240" fill="#d4d0cc" role="img" aria-label="Photo of a living room with a wall-mounted unit"/>
    <polygon points="0,0 1200,0 1200,26 0,40" fill="var(--yellow)"/>
  </svg>
  <div class="t-card">
    <h2>TESTIMONIALS</h2>
    <div class="ph" role="img" aria-label="Customer portrait" style="left:28px;top:86px;width:104px;height:104px;border-radius:50%;background:#9fb4c9"></div>
    <span class="qmark" style="left:150px;top:72px">&ldquo;</span>
    <p class="t-quote">Lorem ipsum dolor sit amet, consectetur adipiscing elit, sed do eiusmod tempor incididunt ut labore et dolore magna aliqua. Ut enim ad minim veniam, quis nostrud exercitation ullamco laboris nisi ut aliquip ex ea commodo consequat.</p>
    <span class="qmark" style="left:684px;top:152px">&rdquo;</span>
    <div class="t-name">John Doe</div>
    <div class="t-co">Company Name</div>
  </div>
  <div class="chev" style="left:108px;top:4226px">&lsaquo;</div>
  <div class="chev" style="left:1072px;top:4226px">&rsaquo;</div>
</section>

<!-- stand behind -->
<section>
  <h2 class="display sec-title" style="top:4442px">We Stand Behind Our Ductless Services</h2>
  <div class="res" style="left:110px"><div class="pic" role="img" aria-label="Photo of a woman pointing a remote at a unit" style="background:linear-gradient(160deg,#eceef0,#b5b9bd)"></div><h4>Get Some Answers</h4><div class="btn">Ductless FAQ</div></div>
  <div class="res" style="left:444px"><div class="pic" role="img" aria-label="Photo of coins and a calculator on paperwork" style="background:linear-gradient(160deg,#b89a6e,#8fa3b3)"></div><h4>Our Financing Options</h4><div class="btn">Financing</div></div>
  <div class="res" style="left:778px"><div class="pic" role="img" aria-label="Photo of a hand holding a remote toward a unit" style="background:linear-gradient(160deg,#f3f3f3,#c9c6c2)"></div><h4>Stay Up to Date</h4><div class="btn">Our Blog</div></div>
</section>

<!-- footer -->
<footer class="footer">
  <div class="f-brand"><span class="brand-mark"></span><span class="brand-name">Copper Fern Services</span></div>
  <div class="f-tag">DUCTLESS EXPERTS</div>
  <div class="social"><span></span><span></span><span></span><span></span><span></span></div>
  <div class="f-div" style="left:444px"></div>
  <div class="f-div" style="left:748px"></div>
  <div class="f-head" style="left:470px">Contact Us</div>
  <div class="f-line" style="left:470px;top:96px"><svg width="12" height="16" viewBox="0 0 10 14"><path d="M5 0a5 5 0 0 1 5 5c0 4-5 9-5 9S0 9 0 5a5 5 0 0 1 5-5z" fill="#fff"/><circle cx="5" cy="5" r="2" fill="#202020"/></svg><span>123&nbsp; Sample Street, New City,<br>Old State, USA.</span></div>
  <div class="f-line" style="left:470px;top:160px"><svg width="14" height="14" viewBox="0 0 24 24"><path d="M5 2h4l2 5-3 2a12 12 0 0 0 7 7l2-3 5 2v4a2 2 0 0 1-2 2A19 19 0 0 1 3 4a2 2 0 0 1 2-2z" fill="#fff"/></svg><span>(+1) 123 456 7890</span></div>
  <div class="f-line" style="left:470px;top:202px"><svg width="14" height="14" viewBox="0 0 24 24"><rect x="2" y="5" width="20" height="14" fill="#fff"/><polyline points="2,5 12,13 22,5" fill="none" stroke="#202020" stroke-width="2"/></svg><span>hello@copperfernservices.com</span></div>
  <div class="f-head" style="left:816px">Newsletter Subscription</div>
  <p class="news-txt">Register your Email Address to get a more Information about us</p>
  <div class="news-input">Email</div>
  <div class="btn" style="left:816px;top:194px;width:102px;height:34px;font-size:12px">Subscribe</div>
  <div class="f-rule"></div>
  <p class="copyright">Copyright © 2019 Copper Fern Services.&nbsp; All Rights Reserved &nbsp;&nbsp; | &nbsp;&nbsp; Privacy Policy.</p>
</footer>

</body>
</html>
```